Marlow Sail Works President Business Card Carbon fiber catamarans

Hi.. I need a new business card design.. I am the President of a high tech yacht builder. We build Carbon Fiber go fast catamarans... Maybe we use the file I am sharing to you as the back of the card.. We need to look cool and crisp ...

Target Market(s)

Affluent People who will purchase a cool yacht

Industry/Entity Type

Custom Yacht Builder

Contact Information for Business Card

Dean Pellway , President, 731.508.2164 USA

Font styles to use
Serif

Requirements
Must have
• the clean crisp cool feel
Nice to have
• clean and crisp
Should not have
• Bold ugly

```html
<!DOCTYPE html>
<html lang="en">
<head>
<meta charset="utf-8">
<title>Marlow Sail Works – Business Card</title>
<link href="https://fonts.googleapis.com/css2?family=Roboto:wght@400;500&display=swap" rel="stylesheet">
<style>
  :root {
    --stage: #2b2b2d;
    --card: #121213;
    --card-edge: #1d1d1f;
    --silver: #d9d9db;
    --silver-soft: #b8b8bb;
    --rule: #6a6a6e;
  }
  * { margin: 0; padding: 0; box-sizing: border-box; }
  html, body {
    width: 1200px; height: 874px; overflow: hidden;
    background: var(--stage);
    font-family: "Roboto", Arial, sans-serif;
  }
  .card-set {
    position: absolute; left: 290px; top: 73px;
    width: 620px; display: flex; flex-direction: column; gap: 20px;
  }
  .card {
    width: 620px; height: 354px;
    background: radial-gradient(ellipse at 40% 30%, var(--card-edge), var(--card) 70%);
    box-shadow: 0 10px 30px rgba(0,0,0,.5);
    position: relative;
  }
  .card-front { display: flex; align-items: center; justify-content: center; }
  .brand { display: flex; align-items: center; gap: 18px; }
  .brand-dot {
    width: 44px; height: 44px; border-radius: 50%;
    border: 0; background: var(--silver-soft);
  }
  .brand-name {
    color: var(--silver); font-weight: 500; font-size: 38px;
    letter-spacing: 6px; text-transform: uppercase;
  }
  .card-back {
    display: flex; align-items: center; justify-content: center;
    padding-top: 40px;
  }
  .person { text-align: right; color: var(--silver-soft); font-size: 15px; line-height: 20px; padding-right: 18px; }
  .person-name { color: var(--silver); font-weight: 500; font-size: 21px; letter-spacing: .5px; margin-bottom: 6px; text-transform: uppercase; }
  .person-title { font-weight: 500; color: var(--silver); }
  .divider { width: 1px; height: 112px; background: var(--rule); }
  .contact-list { list-style: none; padding-left: 14px; color: var(--silver); font-size: 15px; line-height: 21px; }
  .contact-list li { display: flex; align-items: center; gap: 10px; }
  .contact-list svg { width: 12px; height: 12px; fill: var(--silver-soft); flex: none; }
</style>
</head>
<body>
  <main class="card-set">
    <section class="card card-front">
      <div class="brand">
        <span class="brand-dot"></span>
        <span class="brand-name">Marlow Sail Works</span>
      </div>
    </section>

    <section class="card card-back">
      <div class="person">
        <p class="person-name">Dean Pellway</p>
        <p class="person-title">President</p>
        <p>42 Harbor Reach Road</p>
        <p>Newport, Rhode Island 02840</p>
      </div>
      <div class="divider"></div>
      <ul class="contact-list">
        <li><svg viewBox="0 0 12 12"><path d="M2 1l2 0 1 3-1.5 1a7 7 0 0 0 3.5 3.5L8 7l3 1v2a1 1 0 0 1-1 1A9 9 0 0 1 1 2a1 1 0 0 1 1-1z"/></svg>731-508-2164</li>
        <li><svg viewBox="0 0 12 12"><rect x="3" y="0.5" width="6" height="11" rx="1"/></svg>731-508-2170</li>
        <li><svg viewBox="0 0 12 12"><rect x="3" y="1" width="6" height="3"/><rect x="1" y="4" width="10" height="5" rx="1"/><rect x="3" y="8" width="6" height="3"/></svg>731-508-2188</li>
        <li><svg viewBox="0 0 12 12"><path d="M0 2h12v8H0z M0 2l6 5 6-5" /></svg>dean@marlowsail.com</li>
        <li><svg viewBox="0 0 12 12"><circle cx="6" cy="6" r="5.5"/></svg>www.marlowsail.com</li>
      </ul>
    </section>
  </main>
</body>
</html>
```